New travel store signage for Marlow Journeys to attract luxury travellers.

Hello,
We are looking to change the signage of our stores. The signage must include the following:
1. Marlow Journeys Logo (attached)
2. The text...The Travel & Cruise Experts
3. Brand Colours ( Fb0196, 412266, d41d84 and ffffff)
Please note the signage design must be central and only cover two thirds of the store front. We have also attached an image of one of our new stores which might be helpful when preparing a mock up.

We are looking for a quick turnaround on this, making a decision within 48 hours.

Target Market(s)

Retail

Industry/Entity Type

Travel Agency

Font styles to use
Other font styles liked:
• Radley

Colors
E54698
E96AAD
F1A4CE
F9D9EA
FCEFF6
6B429C
8869AF
B7A5CE
E3DAEB
F3F0F8

Requirements
Must have
• Hello, We are looking to change the signage of our stores. The signage must include the following: 1. Marlow Journeys Logo (attached) 2. The text...The Travel & Cruise Experts 3. Brand Colours ( Fb0196, 412266, d41d84 and ffffff) Please note the signage design must be central and only cover two thirds of the store front.
Should not have
• different colour or fonts. Gradient design.

```html
<!DOCTYPE html>
<html lang="en">
<head>
<meta charset="utf-8">
<title>Marlow Journeys – Store Signage</title>
<link href="https://fonts.googleapis.com/css2?family=Radley&display=swap" rel="stylesheet">
<style>
  :root {
    --brand-pink: #fb0196;
    --brand-magenta: #d41d84;
    --brand-purple: #412266;
    --brand-navy: #231a5c;
    --brand-white: #ffffff;
    --backdrop: #eceef0;
  }
  html, body {
    margin: 0;
    padding: 0;
    width: 1200px;
    height: 1200px;
    overflow: hidden;
    background: var(--backdrop);
  }
  .sign {
    position: absolute;
    left: 50px;
    top: 502px;
    width: 1100px;
    height: 195px;
    overflow: hidden;
    box-shadow: 0 18px 30px rgba(60, 70, 90, 0.22);
  }
  .sign-shapes {
    position: absolute;
    inset: 0;
    width: 100%;
    height: 100%;
    display: block;
  }
  .brand-name {
    position: absolute;
    left: 250px;
    top: 118px;
    margin: 0;
    font-family: "Radley", Georgia, serif;
    font-weight: 400;
    font-size: 34px;
    line-height: 1;
    color: var(--brand-purple);
    white-space: nowrap;
  }
  .tagline {
    position: absolute;
    right: 39px;
    top: 44px;
    margin: 0;
    font-family: "Radley", Georgia, serif;
    font-weight: 400;
    color: var(--brand-white);
    text-shadow: 0 2px 3px rgba(40, 10, 50, 0.35);
    text-align: right;
    white-space: nowrap;
  }
  .tagline-row {
    display: block;
    line-height: 1;
  }
  .tagline-row--top {
    border-bottom: 1px solid rgba(255, 255, 255, 0.35);
    padding-bottom: 2px;
  }
  .tagline-small { font-size: 31px; }
  .tagline-large { font-size: 72px; letter-spacing: 1px; }
</style>
</head>
<body>
  <section class="sign" aria-label="Marlow Journeys shop sign">
    <svg class="sign-shapes" viewBox="0 0 1676 297" preserveAspectRatio="none" aria-hidden="true">
      <defs>
        <linearGradient id="field" x1="0" y1="0" x2="1" y2="0">
          <stop offset="0" stop-color="#c8229a"/>
          <stop offset="0.18" stop-color="#4a1a5a"/>
          <stop offset="0.6" stop-color="#5c1f72"/>
          <stop offset="1" stop-color="var(--brand-magenta)"/>
        </linearGradient>
      </defs>
      <rect class="sign-field" width="1676" height="297" fill="url(#field)"/>
      <path class="sign-sweep" d="M 110 297 C 170 180, 260 40, 340 0 L 400 0 C 300 60, 200 200, 170 297 Z" fill="#7a2a8e" opacity="0.55"/>
      <path class="sign-navy-band" d="M 960 0 L 1040 0 C 1010 170, 930 260, 855 297 L 780 297 C 880 240, 960 150, 960 0 Z" fill="var(--brand-navy)"/>
      <path class="sign-panel" d="M 168 297 C 200 140, 290 20, 398 0 L 980 0 C 960 150, 880 250, 792 297 Z" fill="var(--brand-white)"/>
    </svg>
    <p class="brand-name">Marlow Journeys</p>
    <p class="tagline">
      <span class="tagline-row tagline-row--top"><span class="tagline-small">The </span><span class="tagline-large">Travel</span><span class="tagline-small"> &amp;</span></span>
      <span class="tagline-row"><span class="tagline-large">Cruise</span><span class="tagline-small"> Experts</span></span>
    </p>
  </section>
</body>
</html>
```